Maine Organic farm needs a label design for various food products

We need a label design that we can use across a variety of vegetable-based food products that we produce using some of our organic vegetables that we grow on our farm located in Maine, USA.
Our products include:
1) a Traditional and Vegan Korean Kimchi
2) Sumel Sauce (a Korean Hot Sauce)
3) Pickles of Brambleton Relish
4) Brinjalista Chutney
5) Seasonal Soups (many varieties, depending on what's available during the season)
6) Firm Ranks Maple Syrup (we are retired from the Coastal Lancer Guard, hence the name and spelling)
7) Maine Wild Blueberry Kombucha (made with organic Maine wild blueberries)

For the Korean products (kimchi and Sumel Sauce) we would like to incorporate the Korean chili pepper (red) and chopsticks. The attached picture was taken from the internet, it has not been trademarked, but I am hesitant to use it as is as our business expands. Would like the "kimchi" to somehow incorporate the chopstick and pepper, but not look exactly like the attached image.

The final design should communicate farm fresh, organic, healthy and high quality ingredients, and Maine-made. All of our products go into glass jars 16oz and 8 oz. The hot sauce goes into 5.5oz and 8 oz bottles, the Maple Syrup goes into 8oz and 16oz bottles, and a 12oz bottle for the Kombucha. We will need the flexibility of changing some components of the label to accommodate each different food product.

The labels do not have the encircle the entirety of the jar. We understand that this is a tall order to fit so many different products. We are hoping that once we get the feel and design down, we can work with you for a fee outside of the competition to finalize other products labels on different sizes jars, bottles, etc. Its most important that we get the right feel for a label that can be used for a wide variety of food products.

Target Market(s)

Health conscious, foodies, local farm supporters

Font styles to use
Serif
Decorative
Script

Colors

Designer to choose colors to be used in the design.

Requirements
Must have
• Wendle Brook Farm Logo. Room for product name (interchangeable per product), ingredients list, space for jar size (8 oz, 12 oz, 16 oz). On Korean products -must have Korean hot chili pepper and chopsticks
Nice to have
• We'd like something fairly bold and rustic looking.
Should not have
• Nothing too modern or industrial looking. Nothing hippy-ish. Clean and professional. No cartoonish looking letters or designs.

```html
<!DOCTYPE html>
<html lang="en">
<head>
<meta charset="utf-8">
<title>Wendle Brook Farm – Vegan Kimchi Label</title>
<link rel="stylesheet" href="https://fonts.googleapis.com/css2?family=Oswald:wght@400;600&family=Pathway+Gothic+One&family=Yellowtail&family=Parisienne&display=swap">
<style>
  :root {
    --navy: #1f3a58;
    --maroon: #561b24;
    --chili: #c9282d;
    --cream: #f4efe3;
    --parchment-light: #e6d6b0;
    --parchment-dark: #caa978;
    --badge: #e9dcc2;
    --backdrop: #8a96a3;
    --white: #ffffff;
  }
  * { margin: 0; padding: 0; box-sizing: border-box; }
  html, body { width: 927px; height: 1200px; overflow: hidden; }
  body { background: var(--backdrop); position: relative; font-family: "Pathway Gothic One", sans-serif; }

  .label {
    position: absolute; left: 20px; top: 333px;
    width: 887px; height: 534px; overflow: hidden;
    background: radial-gradient(ellipse at 70% 40%, var(--parchment-light), var(--parchment-dark));
  }
  .label-shapes { position: absolute; inset: 0; }

  .brand { position: absolute; left: 56px; top: 88px; width: 372px; text-align: center;
    font-family: "Oswald", sans-serif; font-weight: 600; color: var(--navy); line-height: 1; }
  .brand-name { font-size: 46px; letter-spacing: 1px; }
  .brand-farm { font-size: 24px; letter-spacing: 8px; margin-top: 6px; }

  .product-type { position: absolute; left: 150px; top: 235px; width: 210px; text-align: center;
    font-family: "Oswald", sans-serif; font-weight: 600; font-size: 64px; color: var(--navy); line-height: 1; }
  .product-name { position: absolute; left: 110px; top: 290px;
    font-family: "Yellowtail", cursive; font-size: 112px; color: var(--chili); line-height: 1; }

  .net-weight { position: absolute; left: 440px; top: 422px; width: 76px; text-align: center;
    font-family: "Oswald", sans-serif; font-size: 19px; color: var(--navy); line-height: 1.2; }

  .info { position: absolute; left: 527px; width: 356px; text-align: center; color: var(--navy); }
  .ingredients { top: 66px; font-size: 16.5px; line-height: 1.45; }
  .made-in { top: 190px; font-family: "Parisienne", cursive; font-size: 44px; line-height: 1; }
  .storage { top: 240px; font-size: 18px; }
  .about-title { top: 293px; font-family: "Oswald", sans-serif; font-size: 24px; line-height: 1; }
  .about-text { top: 330px; font-size: 16px; line-height: 1.45; }

  .contact { position: absolute; left: 538px; top: 390px; width: 332px; height: 110px;
    background: var(--white); color: var(--maroon); text-align: center;
    font-family: "Oswald", sans-serif; font-size: 19px; line-height: 1.45; padding-top: 10px; }
</style>
</head>
<body>
  <section class="label">
    <svg class="label-shapes" width="887" height="534" viewBox="0 0 887 534">
      <circle cx="250" cy="190" r="306" fill="var(--maroon)"/>
      <circle cx="234" cy="176" r="300" fill="var(--cream)"/>
      <rect role="img" aria-label="Pale honeycomb dot pattern across the top of the light panel" x="0" y="0" width="460" height="150" fill="var(--cream)" opacity="0.6"/>
      <rect role="img" aria-label="Faint sketch of a red barn, windmill and fence in the farm fields" x="0" y="235" width="520" height="220" fill="#e2ddd2" opacity="0.55"/>
      <rect role="img" aria-label="Red Korean chili pepper crossed with a pair of chopsticks" x="92" y="275" width="90" height="150" fill="#e8cfc9" opacity="0.55"/>
      <circle cx="242" cy="136" r="94" fill="var(--badge)"/>
    </svg>

    <div class="brand">
      <div class="brand-name">WENDLE BROOK</div>
      <div class="brand-farm">FARM</div>
    </div>

    <div class="product-type">VEGAN</div>
    <div class="product-name">Kimchi</div>

    <div class="net-weight">Netwt<br>16oz/375<br>Grams</div>

    <p class="info ingredients">Local Chinese Cabbage, Sea Salt, Filtered Water<br>local Green Onions, local Ginger, Garlic,<br>Korean Chili Flakes, Korean Chili Powder,<br>Hawaiian Chili Peppers, Maui Sugar, &amp; Aloha</p>
    <p class="info made-in">Made in Maine</p>
    <p class="info storage">Keep refrigerated after opening</p>
    <p class="info about-title">WENDLE BROOK FARM:</p>
    <p class="info about-text">A Veteran-owned, Livestock and Organically<br>certified vegetable farm located in Dunmore, Maine.</p>

    <div class="contact">
      email:hello@wendlebrookfarm.com<br>
      WWW.WENDLEBROOKFARM.COM<br>
      Call: 000 0000 000
    </div>
  </section>
</body>
</html>
```